physical therapy flyer

2 office locations speciality programs - work injury / Motor vehicle accidents - spanish speaking - do not put balance defecits/ fall prevention - Spanish speaking
neck and back pain shoulder pain/ rotator cuff disorder / bursitis
hip pain knee andle and foot pain post operative care including Spine , shoulder , knee , total joint replacement

Meadowlark Physical therapy & Chiropractic
4871 Pinecrest BLvd
dalton heights ny 10592
7185820147
3715 Tillman Parkway
Fernvale NY 10592
7189043218
www.meadowlarkptrehab.com

```html
<!DOCTYPE html>
<html lang="en">
<head>
<meta charset="utf-8">
<title>Meadowlark Physical therapy &amp; Chiropractic</title>
<link rel="stylesheet" href="https://fonts.googleapis.com/css2?family=Poppins:wght@400;500;600;700&family=Bebas+Neue&family=Open+Sans:wght@400&display=swap">
<style>
  :root {
    --green-deep: #087d36;
    --green-head: #0f7f34;
    --green-lime: #6cb33f;
    --green-soft: #92d255;
    --green-ring: #b9dea0;
    --badge-ink: #0b5a26;
    --ink: #1f2121;
    --hero-bg: #eff0f1;
    --paper: #ffffff;
    --pin: #e5262d;
  }
  * { margin: 0; padding: 0; box-sizing: border-box; }
  html, body { width: 955px; height: 1200px; overflow: hidden; background: var(--paper); }
  body { font-family: "Poppins", sans-serif; color: var(--ink); position: relative; }
  .flyer { position: absolute; inset: 0; width: 955px; height: 1200px; background: var(--paper); overflow: hidden; }

  .hero { position: absolute; left: 0; top: 0; width: 955px; height: 406px; background: var(--hero-bg); }
  .hero-photo { position: absolute; left: 442px; top: 0; width: 513px; height: 406px;
    background: linear-gradient(120deg, #e9e6e2 0%, #d9c2b0 35%, #c9c9c9 60%, #eef0ee 100%); }

  .brand { position: absolute; left: 63px; top: 66px; display: flex; align-items: center; gap: 10px; }
  .brand-dot { width: 44px; height: 44px; border-radius: 50%; background: var(--ink); flex: none; }
  .brand-name { font-family: "Open Sans", sans-serif; font-size: 16.5px; line-height: 1.12; color: var(--ink); }

  .headline { position: absolute; left: 63px; top: 150px; font-weight: 700; font-size: 42px; line-height: 49px; color: var(--green-head); letter-spacing: -0.3px; }
  .headline .amp { font-weight: 400; color: var(--ink); }
  .headline .dark { color: var(--ink); }

  .tagline { position: absolute; left: 63px; top: 334px; padding-left: 11px; border-left: 4px solid var(--green-deep);
    font-weight: 500; font-size: 19.5px; line-height: 27px; color: var(--ink); }

  .badge { position: absolute; left: 703px; top: 296px; width: 220px; height: 220px; }
  .badge-text { position: absolute; inset: 0; display: flex; flex-direction: column; align-items: center; justify-content: center; text-align: center; }
  .badge-big { font-family: "Bebas Neue", sans-serif; font-size: 36px; line-height: 31px; color: var(--badge-ink); }
  .badge-small { font-family: "Poppins", sans-serif; font-size: 16px; line-height: 17px; color: var(--paper); margin-top: 4px; }

  .rehab { position: absolute; left: 0; top: 406px; width: 381px; height: 490px; background: var(--green-deep);
    border-bottom-right-radius: 26px; overflow: hidden; }
  .rehab-title { position: absolute; left: 61px; top: 16px; font-weight: 700; font-size: 21px; line-height: 26px; color: var(--green-soft); }
  .rehab-list { position: absolute; left: 61px; top: 90px; width: 300px; list-style: none;
    display: grid; grid-template-columns: 98px 1fr; row-gap: 14px; color: var(--paper); font-size: 16px; line-height: 20px; }
  .rehab-list li { display: flex; gap: 5px; align-items: flex-start; }
  .tick { width: 11px; height: 11px; margin-top: 4px; flex: none; }
  .rehab-photo { position: absolute; left: 0; top: 172px; width: 381px; height: 318px;
    background: linear-gradient(160deg, rgba(8,125,54,0) 0%, #4f7d86 35%, #2f5f72 60%, #276f4b 100%); }

  .treat-title { position: absolute; left: 417px; top: 424px; font-weight: 700; font-size: 21px; line-height: 26px; color: var(--green-head); }
  .treat-list { position: absolute; left: 415px; top: 498px; width: 460px; list-style: none; }
  .treat-item { position: absolute; left: 0; display: flex; align-items: center; }
  .treat-icon { width: 64px; height: 64px; border-radius: 50%; background: var(--green-lime); border: 4px solid var(--green-ring); flex: none; }
  .treat-label { position: absolute; left: 85px; font-size: 19.5px; line-height: 23px; width: 300px; color: var(--ink); }
  .rule { position: absolute; left: 500px; width: 366px; border-top: 1.2px dashed #555; }

  .loc-head { position: absolute; left: 59px; top: 910px; font-weight: 600; font-size: 21px; color: var(--green-lime); }
  .loc-line { position: absolute; left: 258px; top: 928px; width: 621px; height: 1.5px; background: var(--green-lime); }
  .loc { position: absolute; top: 954px; }
  .loc-name { font-weight: 600; font-size: 19px; color: var(--green-deep); line-height: 26px; }
  .loc-row { display: flex; gap: 6px; font-size: 18px; line-height: 22px; color: var(--ink); margin-top: 8px; }
  .loc-row svg { flex: none; margin-top: 4px; }
  .loc-phone { margin-top: 20px; }
  .loc-divider { position: absolute; left: 422px; top: 1000px; width: 5px; height: 70px; background: var(--green-lime); }

  .visit { position: absolute; left: 59px; top: 1096px; width: 831px; height: 44px; border-radius: 22px; background: var(--green-deep);
    display: flex; align-items: center; padding-left: 33px; color: var(--paper); }
  .visit-lead { font-size: 14.5px; letter-spacing: 5px; }
  .visit-bar { width: 1.5px; height: 12px; background: var(--green-soft); margin: 0 15px 0 10px; }
  .visit-url { font-size: 22px; letter-spacing: 4.3px; }
  .visit-url b { font-weight: 700; }
</style>
</head>
<body>
<main class="flyer">
  <section class="hero">
    <div class="hero-photo" role="img" aria-label="Photo of a therapist gently stretching a relaxed patient's neck in a bright clinic"></div>

    <div class="brand">
      <span class="brand-dot"></span>
      <p class="brand-name">Meadowlark Physical Therapy,<br>Chiropractic, and Acupuncture</p>
    </div>

    <h1 class="headline">Meadowlark<br>Physical therapy<br><span class="amp">&amp;</span> <span class="dark">Chiropractic</span></h1>

    <p class="tagline">Comprehensive Care Across<br>Two Locations!</p>
  </section>

  <div class="badge">
    <svg width="220" height="220" viewBox="0 0 220 220" aria-hidden="true">
      <g fill="var(--green-lime)">
        <circle cx="110" cy="110" r="100"/>
        <circle cx="206" cy="110" r="14"/><circle cx="201.3" cy="139.7" r="14"/><circle cx="187.7" cy="166.4" r="14"/>
        <circle cx="166.4" cy="187.7" r="14"/><circle cx="139.7" cy="201.3" r="14"/><circle cx="110" cy="206" r="14"/>
        <circle cx="80.3" cy="201.3" r="14"/><circle cx="53.6" cy="187.7" r="14"/><circle cx="32.3" cy="166.4" r="14"/>
        <circle cx="18.7" cy="139.7" r="14"/><circle cx="14" cy="110" r="14"/><circle cx="18.7" cy="80.3" r="14"/>
        <circle cx="32.3" cy="53.6" r="14"/><circle cx="53.6" cy="32.3" r="14"/><circle cx="80.3" cy="18.7" r="14"/>
        <circle cx="110" cy="14" r="14"/><circle cx="139.7" cy="18.7" r="14"/><circle cx="166.4" cy="32.3" r="14"/>
        <circle cx="187.7" cy="53.6" r="14"/><circle cx="201.3" cy="80.3" r="14"/>
      </g>
      <circle cx="110" cy="110" r="93" fill="none" stroke="#ffffff" stroke-width="1.5"/>
    </svg>
    <div class="badge-text">
      <span class="badge-big">SPANISH<br>SPEAKING</span>
      <span class="badge-small">SERVICES<br>AVAILABLE</span>
    </div>
  </div>

  <section class="rehab">
    <h2 class="rehab-title">Post-Surgical<br>Rehabilitation</h2>
    <ul class="rehab-list">
      <li><svg class="tick" viewBox="0 0 12 12"><circle cx="6" cy="6" r="6" fill="var(--green-soft)"/><path d="M3.3 6.2l1.8 1.8 3.6-3.6" stroke="var(--green-deep)" stroke-width="1.5" fill="none"/></svg>Spine</li>
      <li><svg class="tick" viewBox="0 0 12 12"><circle cx="6" cy="6" r="6" fill="var(--green-soft)"/><path d="M3.3 6.2l1.8 1.8 3.6-3.6" stroke="var(--green-deep)" stroke-width="1.5" fill="none"/></svg>&nbsp;Knee</li>
      <li><svg class="tick" viewBox="0 0 12 12"><circle cx="6" cy="6" r="6" fill="var(--green-soft)"/><path d="M3.3 6.2l1.8 1.8 3.6-3.6" stroke="var(--green-deep)" stroke-width="1.5" fill="none"/></svg>Shoulder</li>
      <li><svg class="tick" viewBox="0 0 12 12"><circle cx="6" cy="6" r="6" fill="var(--green-soft)"/><path d="M3.3 6.2l1.8 1.8 3.6-3.6" stroke="var(--green-deep)" stroke-width="1.5" fill="none"/></svg>Total Joint<br>Replacements</li>
    </ul>
    <div class="rehab-photo" role="img" aria-label="Photo of a therapist supporting an older patient's lower back during rehabilitation"></div>
  </section>

  <h2 class="treat-title">Specialized<br>Treatment for</h2>
  <ul class="treat-list">
    <li class="treat-item" style="top:0"><span class="treat-icon" role="img" aria-label="Icon of an injured worker"></span><span class="treat-label" style="top:18px">Work-Related Injuries</span></li>
    <li class="treat-item" style="top:94px"><span class="treat-icon" role="img" aria-label="Icon of a car accident"></span><span class="treat-label" style="top:8px">Motor Vehicle Accident<br>Recovery</span></li>
    <li class="treat-item" style="top:211px"><span class="treat-icon" role="img" aria-label="Icon of neck and back pain"></span><span class="treat-label" style="top:8px">Neck, Back, and<br>Shoulder Pain</span></li>
    <li class="treat-item" style="top:329px"><span class="treat-icon" role="img" aria-label="Icon of foot and ankle pain"></span><span class="treat-label" style="top:0">Hip, Knee, Ankle, and<br>Foot Pain</span></li>
  </ul>
  <div class="rule" style="top:571px"></div>
  <div class="rule" style="top:686px"></div>
  <div class="rule" style="top:799px"></div>

  <h2 class="loc-head">Our Locations</h2>
  <div class="loc-line"></div>

  <div class="loc" style="left:61px">
    <h3 class="loc-name">DALTON HEIGHTS</h3>
    <p class="loc-row"><svg width="11" height="14" viewBox="0 0 11 14"><path d="M5.5 0A5.5 5.5 0 0 0 0 5.5C0 9.5 5.5 14 5.5 14S11 9.5 11 5.5A5.5 5.5 0 0 0 5.5 0zm0 7.7a2.2 2.2 0 1 1 0-4.4 2.2 2.2 0 0 1 0 4.4z" fill="var(--pin)"/></svg><span>4871 Pinecrest BLvd<br>dalton heights ny 10592</span></p>
    <p class="loc-row loc-phone"><svg width="12" height="12" viewBox="0 0 12 12"><path d="M2.4 0.6l2 2.2-1 1.4c.7 1.5 1.9 2.7 3.4 3.4l1.4-1 2.2 2-1 2C5.5 10.6 1.4 6.5 0.4 1.6z" fill="var(--green-lime)"/></svg><span>7185820147</span></p>
  </div>

  <div class="loc-divider"></div>

  <div class="loc" style="left:476px">
    <h3 class="loc-name">FERNVALE</h3>
    <p class="loc-row"><svg width="11" height="14" viewBox="0 0 11 14"><path d="M5.5 0A5.5 5.5 0 0 0 0 5.5C0 9.5 5.5 14 5.5 14S11 9.5 11 5.5A5.5 5.5 0 0 0 5.5 0zm0 7.7a2.2 2.2 0 1 1 0-4.4 2.2 2.2 0 0 1 0 4.4z" fill="var(--pin)"/></svg><span>3715 Tillman Parkway<br>Fernvale NY 10592</span></p>
    <p class="loc-row loc-phone"><svg width="12" height="12" viewBox="0 0 12 12"><path d="M2.4 0.6l2 2.2-1 1.4c.7 1.5 1.9 2.7 3.4 3.4l1.4-1 2.2 2-1 2C5.5 10.6 1.4 6.5 0.4 1.6z" fill="var(--green-lime)"/></svg><span>7189043218</span></p>
  </div>

  <div class="visit">
    <span class="visit-lead">VISIT US AT</span>
    <span class="visit-bar"></span>
    <span class="visit-url">www.<b>meadowlarkptrehab</b>.com</span>
  </div>
</main>
</body>
</html>
```